my website is tavorinque.com. (brand name is ta belle vitrine) This is just a template that i have choose for. The content and the pictures are not about my business just the template.
I would like to have 4 pages for now. 1 homepage, which will be an overview for all pages, it is right now in this way. It will directly highlight my story. My website will tell an exclusive story about details which makes the difference and will make people happy with very small things. It will be art related but very stylish as well. I also want to have a event agenda on my homepage where people can see where my next event is. Page 2 my blog, where I will write weekly about mindset, lifestyle and details. Inspiration place for people who are looking for unique and exclusive approaches in life. Page 3 shop, where I will sell my stuff which is handmade and unique, it will be limited edition stuff. Mostly I will make the designs from marbling art, which I am a teacher for. (https://www.vidoranta.com/watch?v=KpwuzRaxTmo) check this video out for more. Page 4 is book page. Here people will be able to book private or group classes for marbling art (check the video). I have already a community of more than 500 people on gath rix, which will be my public as well. I wanna implement the gath rix button on this page as well. to be able to track.

This is about my website. I also need a logo for my brand, which will suit my website and my goals.

I can also give you a reference website, which really like as structure and style;
https://www.brightorvalco.com/products/the-morning-ledger?gclid=Xr4TpLmwq2HsVD9KEBsZTrc-WkPhyQ-uvlEjdRs3NKaOYFCBWMpuTzG8xyCVbhdnLWRqoaNf_2e8ZtpRvHbAwq9FLQ_hqgQ

Logo Text

ta belle vitrine

Coding

Coded - Design and coding required

Number of Pages Required

4 page

Requirements
Must have
• I can also give you a reference website, which really like as structure and style;
• https://www.brightorvalco.com/products/the-morning-ledger?gclid=Xr4TpLmwq2HsVD9KEBsZTrc-WkPhyQ-uvlEjdRs3NKaOYFCBWMpuTzG8xyCVbhdnLWRqoaNf_2e8ZtpRvHbAwq9FLQ_hqgQ

```html
<!DOCTYPE html>
<html lang="en">
<head>
<meta charset="utf-8">
<title>ta belle vitrine</title>
<link href="https://fonts.googleapis.com/css2?family=Open+Sans:ital,wght@0,400;0,600;0,700;0,800;1,400&display=swap" rel="stylesheet">
<style>
:root{
  --ink:#111111;
  --black:#141210;
  --white:#ffffff;
  --panel:#f2f2f2;
  --text:#444444;
  --muted:#666666;
  --rule:#d6d6d6;
  --field:#bdbdbd;
  --price:#f4b400;
}
*{box-sizing:border-box;margin:0;padding:0}
html,body{width:1200px;height:3130px;overflow:hidden}
body{position:relative;background:var(--white);font-family:"Open Sans",Arial,sans-serif;color:var(--text)}
.abs{position:absolute}
.heading{font-weight:800;color:var(--ink);letter-spacing:2px;text-align:center;font-size:33px;width:100%}
.rule{position:absolute;height:6px;width:140px;background:var(--rule);left:530px}
.btn{position:absolute;border:3px solid var(--ink);background:transparent;font-weight:700;font-size:14px;letter-spacing:1px;color:var(--ink);display:flex;align-items:center;justify-content:center}

/* header */
.site-header{left:0;top:0;width:1200px;height:90px;background:var(--white)}
.nav-link{position:absolute;top:36px;font-size:14px;font-weight:700;color:var(--ink);letter-spacing:.5px}
.brand{position:absolute;left:520px;top:20px;display:flex;align-items:center;gap:10px}
.brand-mark{width:44px;height:44px;border-radius:50%;border:2px solid var(--ink)}
.brand-name{font-size:20px;font-weight:400;color:var(--ink)}

/* hero */
.hero{left:0;top:90px;width:1200px;height:555px;background:var(--black)}
.hero-photo{position:absolute;left:437px;top:0;width:763px;height:555px;background:linear-gradient(160deg,#a13a3a 0%,#4e6b3a 25%,#7fb4c4 50%,#c86f9e 70%,#9fc0c9 100%)}
.story-card{position:absolute;left:77px;top:64px;width:510px;height:428px;background:var(--white);padding:40px 32px}
.story-card h1{font-size:54px;font-weight:800;color:var(--ink);letter-spacing:1px;line-height:1}
.story-card .card-rule{width:140px;height:6px;background:var(--rule);margin:18px 0 20px}
.story-card p{font-size:15.5px;line-height:28px;color:var(--text)}

/* shop */
.shop-card{position:absolute;top:812px;width:303px;height:345px;background:var(--black)}
.shop-card .photo{height:240px}
.shop-card .name{color:var(--white);font-weight:700;font-size:15px;text-align:center;margin-top:28px;letter-spacing:.5px}
.shop-card .price{color:var(--price);font-weight:700;font-size:16px;text-align:center;margin-top:8px}
.arrow{position:absolute;top:966px}

/* booking */
.booking{left:0;top:1248px;width:1200px;height:497px;background:var(--panel)}
.booking-photo{position:absolute;left:0;top:0;width:589px;height:497px;background:radial-gradient(circle at 40% 55%,#b67c8e 0%,#8e5a66 45%,#5b3a3f 100%)}
.booking h2{position:absolute;left:612px;top:48px;font-size:33px;font-weight:800;color:var(--ink);letter-spacing:1px}
.booking .b-rule{position:absolute;left:612px;top:101px;width:140px;height:6px;background:var(--rule)}
.booking .intro{position:absolute;left:614px;top:128px;width:520px;font-size:13.5px;font-style:italic;line-height:24px;color:var(--muted)}
.field{position:absolute;height:38px;border:2px solid var(--field);background:var(--panel);font-size:12.5px;color:var(--muted);padding:8px 12px}

/* blog */
.post{position:absolute;top:1903px;width:332px}
.post .photo{height:232px}
.post h3{font-size:16.5px;font-weight:800;color:var(--ink);margin-top:24px;letter-spacing:.3px}
.post p{font-size:15px;line-height:23px;color:var(--text);margin-top:6px}
.post .date{font-size:13px;color:var(--text);margin-top:6px;display:flex;align-items:center;gap:8px}

/* events */
.events{left:0;top:2321px;width:1200px;height:459px;background:var(--panel)}
.event-photo{position:absolute;left:138px;top:144px;width:424px;height:259px;background:linear-gradient(135deg,#5c4a3a 0%,#7a4f83 40%,#c9b6cf 65%,#8a6a2e 100%)}
.event-body{position:absolute;left:589px;top:144px;width:500px}
.event-body h3{font-size:16.5px;font-weight:800;color:var(--ink);letter-spacing:.3px}
.event-body .date{font-size:13px;margin-top:8px;display:flex;align-items:center;gap:8px}
.event-body p{font-size:15px;line-height:24px;margin-top:6px}

/* subscribe */
.subscribe{left:0;top:2780px;width:1200px;height:221px;background:var(--black)}
.subscribe h2{color:var(--white);font-size:23px;font-weight:700;letter-spacing:1px;text-align:center;margin-top:50px}
.subscribe .s-rule{position:absolute;left:531px;top:82px;width:138px;height:6px;background:var(--white)}
.sub-form{position:absolute;left:342px;top:117px;width:513px;height:56px;background:var(--white);border:4px solid var(--white);outline:2px solid #888;display:flex;align-items:center}
.sub-form .placeholder{flex:1;font-size:13px;color:var(--muted);display:flex;align-items:center;gap:12px;padding-left:16px}
.sub-form .go{background:#2a2a2a;color:var(--white);font-weight:700;font-size:14px;letter-spacing:1px;width:120px;height:40px;display:flex;align-items:center;justify-content:center;margin-right:4px}

/* footer */
.site-footer{left:0;top:3001px;width:1200px;height:129px;background:var(--white);text-align:center}
.site-footer .copy{font-size:12.5px;color:var(--muted);margin-top:42px}
.social{display:flex;justify-content:center;gap:22px;margin-top:12px}
.social span{width:18px;height:18px;border-radius:50%;background:#555}
</style>
</head>
<body>

<header class="abs site-header">
  <span class="nav-link" style="left:254px">HOME</span>
  <span class="nav-link" style="left:354px">MY BLOG</span>
  <div class="brand"><span class="brand-mark"></span><span class="brand-name">ta belle vitrine</span></div>
  <span class="nav-link" style="left:788px">SHOP</span>
  <span class="nav-link" style="left:884px">BOOK</span>
  <svg class="abs" style="left:1074px;top:38px" width="16" height="14" viewBox="0 0 16 14"><path d="M0 1h3l2 8h9l2-6H4" fill="none" stroke="#111" stroke-width="2"/><circle cx="6" cy="12" r="1.5" fill="#111"/><circle cx="13" cy="12" r="1.5" fill="#111"/></svg>
  <svg class="abs" style="left:1115px;top:38px" width="12" height="14" viewBox="0 0 12 14"><circle cx="6" cy="4" r="3.5" fill="#111"/><path d="M0 14c0-5 3-6 6-6s6 1 6 6z" fill="#111"/></svg>
</header>

<section class="abs hero">
  <div class="hero-photo" role="img" aria-label="Marbling tray with floral paint pattern and paint jars"></div>
  <div class="story-card">
    <h1>MY STORY</h1>
    <div class="card-rule"></div>
    <p>Ta belle vitrine is a leading Online Store. We provide an unparalleled selection of the very best quality products, an easy and comfortable shopping experience, expedited shipping offers, and exceptional customer service. Check out our collection of new arrivals, best-sellers, and clearance items today.</p>
    <div class="btn" style="left:32px;top:331px;width:159px;height:46px">READ MORE</div>
  </div>
</section>

<h2 class="abs heading" style="top:700px">MY SHOP</h2>
<div class="rule" style="top:757px"></div>
<svg class="arrow" style="left:74px" width="16" height="30" viewBox="0 0 16 30"><path d="M14 2L3 15l11 13" fill="none" stroke="#777" stroke-width="3"/></svg>
<svg class="arrow" style="left:1111px" width="16" height="30" viewBox="0 0 16 30"><path d="M2 2l11 13L2 28" fill="none" stroke="#777" stroke-width="3"/></svg>
<div class="shop-card" style="left:136px"><div class="photo" role="img" aria-label="Brown marbled paper in tray" style="background:linear-gradient(160deg,#6a4a3c,#8a5a4a 50%,#c7bfb5)"></div><div class="name">PRODUCT NAME</div><div class="price">€40.00</div></div>
<div class="shop-card" style="left:449px"><div class="photo" role="img" aria-label="Dark marbling tray with paint rings" style="background:linear-gradient(160deg,#9a8f88,#2b2726 45%,#1a1818)"></div><div class="name">PRODUCT NAME</div><div class="price">€40.00</div></div>
<div class="shop-card" style="left:762px"><div class="photo" role="img" aria-label="Purple and white marbled pattern" style="background:linear-gradient(160deg,#6d5a3f,#7a4f83 50%,#d8cbe0)"></div><div class="name">PRODUCT NAME</div><div class="price">€40.00</div></div>

<section class="abs booking">
  <div class="booking-photo" role="img" aria-label="Hand drawing a marbling pattern with a stylus"></div>
  <h2>ONLINE BOOK</h2>
  <div class="b-rule"></div>
  <p class="intro">For general comments and inquiries, please get in touch with us with the form below.</p>
  <div class="field" style="left:614px;top:201px;width:248px">Enter Name</div>
  <div class="field" style="left:877px;top:201px;width:250px">Phone No.</div>
  <div class="field" style="left:614px;top:246px;width:248px">Email Address</div>
  <div class="field" style="left:877px;top:246px;width:250px">Subject</div>
  <div class="field" style="left:614px;top:292px;width:513px;height:73px">Message</div>
  <div class="btn" style="left:614px;top:382px;width:160px;height:48px">SUBMIT</div>
</section>

<h2 class="abs heading" style="top:1796px">MY BLOG</h2>
<div class="rule" style="top:1853px"></div>
<article class="post" style="left:75px"><div class="photo" role="img" aria-label="Floral marbling tray" style="background:linear-gradient(160deg,#4e6b3a,#7fb4c4 50%,#c86f9e)"></div><h3>LOREM IPSUM DOLOR SIT</h3><p>Vestibulum ante ipsum primis in faucibus orci luctus et ultrices posuere.</p><div class="date"><svg width="12" height="12" viewBox="0 0 12 12"><rect x="1" y="2" width="10" height="9" fill="none" stroke="#444" stroke-width="1.5"/><path d="M1 5h10" stroke="#444"/></svg>Oct 04, 2017</div></article>
<article class="post" style="left:436px"><div class="photo" role="img" aria-label="Brown marbled paper in tray" style="background:linear-gradient(160deg,#6a4a3c,#8a5a4a 50%,#c7bfb5)"></div><h3>LOREM IPSUM DOLOR SIT</h3><p>Vestibulum ante ipsum primis in faucibus orci luctus et ultrices posuere.</p><div class="date"><svg width="12" height="12" viewBox="0 0 12 12"><rect x="1" y="2" width="10" height="9" fill="none" stroke="#444" stroke-width="1.5"/><path d="M1 5h10" stroke="#444"/></svg>Oct 04, 2017</div></article>
<article class="post" style="left:797px"><div class="photo" role="img" aria-label="Dark marbling tray with paint jars" style="background:linear-gradient(160deg,#9a8f88,#2b2726 45%,#1a1818)"></div><h3>LOREM IPSUM DOLOR SIT</h3><p>Vestibulum ante ipsum primis in faucibus orci luctus et ultrices posuere.</p><div class="date"><svg width="12" height="12" viewBox="0 0 12 12"><rect x="1" y="2" width="10" height="9" fill="none" stroke="#444" stroke-width="1.5"/><path d="M1 5h10" stroke="#444"/></svg>Oct 04, 2017</div></article>

<section class="abs events">
  <h2 class="heading" style="position:absolute;top:40px">UPCOMING EVENTS</h2>
  <div class="rule" style="top:97px"></div>
  <div class="event-photo" role="img" aria-label="Marbling tray with purple and white pattern"></div>
  <div class="event-body">
    <h3>LOREM IPSUM DOLOR SIT VESTIBULUM PURUS ..</h3>
    <div class="date"><svg width="12" height="12" viewBox="0 0 12 12"><rect x="1" y="2" width="10" height="9" fill="none" stroke="#444" stroke-width="1.5"/><path d="M1 5h10" stroke="#444"/></svg>Oct 04, 2017</div>
    <p>Vestibulum ante ipsum primis in faucibus orci luctus et ultrices posuere. Aenean a nibh eget turpis vehicula tempus ac sed massa. Vestibulum dolor nulla, ultrices ac tincidunt sed, laoreet non est. Suspendisse lobortis turpis in odio blandit ac interdum lorem euismod. Etiam risus massa, vulputate eu pellentesque et, consectetur a neque.</p>
  </div>
  <div class="btn" style="left:589px;top:355px;width:157px;height:48px">READ MORE</div>
</section>

<section class="abs subscribe">
  <h2>EMAIL SUBSCRIBE</h2>
  <div class="s-rule"></div>
  <div class="sub-form">
    <div class="placeholder"><svg width="13" height="10" viewBox="0 0 13 10"><rect width="13" height="10" fill="#444"/><path d="M0 0l6.5 5L13 0" fill="none" stroke="#fff"/></svg>Email Address</div>
    <div class="go">SUBSCRIBE</div>
  </div>
</section>

<footer class="abs site-footer">
  <p class="copy">Copyright © 2017. Company Name. All Right Reserved</p>
  <div class="social"><span></span><span></span><span></span><span></span></div>
</footer>

</body>
</html>
```